professional business card design

Business card design. Photos have been uploaded and i am open to the designer choosing which photos to use. Would like the card to be mostyly in a grey scale design with black, whites, silver & grey colours. I have added copy of our flyer as would like on the back side of card our services to be listed. Do not use any bright colurs such as blue red green or yellow. i need to be able to edit the phone number and naem in the final card design submitted.

Target Market(s)

Clients

Industry/Entity Type

earhmovibng and transport

Contact Information for Business Card

Director Name, address, email, phone number and services

Colors

Designer to choose only greyscale colors for use in the design.

Requirements
Should not have
• no yellow, red, blue or green

```html
<!DOCTYPE html>
<html lang="en">
<head>
<meta charset="utf-8">
<title>Ridgeway Haulage – Business Card</title>
<link href="https://fonts.googleapis.com/css2?family=Archivo+Black&family=Arimo:ital,wght@0,400;0,700;1,400&display=swap" rel="stylesheet">
<style>
  :root {
    --page: #c9c9c9;
    --black: #0b0b0b;
    --charcoal: #1c1c1c;
    --graphite: #3a3a3a;
    --silver-light: #e6e6e6;
    --silver-mid: #b9b9b9;
    --silver-dark: #8f8f8f;
    --white: #ffffff;
    --ink: #111111;
  }
  * { box-sizing: border-box; margin: 0; padding: 0; }
  html, body { width: 1200px; height: 800px; overflow: hidden; }
  body {
    background: var(--page);
    font-family: "Arimo", Arial, sans-serif;
    display: flex; align-items: center; justify-content: center; gap: 36px;
  }
  .card {
    position: relative; width: 560px; height: 320px; overflow: hidden;
    background: var(--black);
    box-shadow: 0 10px 24px rgba(0,0,0,.28);
  }
  .texture {
    position: absolute; left: 0; top: 0; width: 100%;
    background: radial-gradient(ellipse at 40% 35%, var(--graphite) 0%, var(--charcoal) 45%, var(--black) 100%);
  }
  .silver {
    background: linear-gradient(180deg, var(--silver-light) 0%, var(--silver-mid) 55%, var(--silver-dark) 100%);
    color: var(--ink);
  }
  .brand-name {
    font-family: "Arimo", Arial, sans-serif; font-weight: 700; color: var(--white);
    letter-spacing: 1px; text-transform: uppercase;
  }

  /* Front */
  .front .texture { height: 172px; }
  .front .truck-photo {
    position: absolute; left: 230px; top: 0; width: 330px; height: 190px;
    background: linear-gradient(160deg, #2b2b2b 0%, #6b6b6b 45%, #a8a8a8 70%, #4a4a4a 100%);
  }
  .front .brand-name { position: absolute; left: 28px; top: 62px; font-size: 30px; line-height: 1.05; }
  .front .identity-band {
    position: absolute; left: 0; top: 172px; width: 100%; height: 64px;
    display: flex; align-items: center; padding: 0 26px;
  }
  .person { width: 210px; }
  .person-name { font-weight: 700; font-size: 22px; letter-spacing: .5px; text-transform: uppercase; }
  .person-role { font-size: 13px; letter-spacing: 1px; text-transform: uppercase; text-align: right; color: var(--graphite); }
  .divider { width: 1px; height: 42px; background: var(--graphite); margin: 0 18px; }
  .links { font-size: 14px; line-height: 1.6; text-transform: uppercase; }
  .links div { display: flex; align-items: center; gap: 8px; }
  .links svg { width: 14px; height: 14px; }
  .front .phone-band {
    position: absolute; left: 0; top: 236px; width: 100%; height: 44px;
    display: flex; align-items: center; gap: 14px; padding: 0 26px;
    color: var(--white);
  }
  .phone-icon { width: 28px; height: 28px; border-radius: 6px; background: var(--graphite); display: flex; align-items: center; justify-content: center; }
  .phone-icon svg { width: 16px; height: 16px; }
  .phone-number { font-weight: 700; font-size: 27px; letter-spacing: 2px; }
  .front .address-band {
    position: absolute; left: 0; top: 280px; width: 100%; height: 40px;
    display: flex; align-items: center; padding: 0 26px;
    font-size: 16px; letter-spacing: .5px; text-transform: uppercase;
  }

  /* Back */
  .back .texture { height: 124px; }
  .back .brand-name { position: absolute; left: 0; top: 40px; width: 100%; text-align: center; font-size: 32px; }
  .back .services-title-band {
    position: absolute; left: 0; top: 118px; width: 100%; height: 34px;
    display: flex; align-items: center; justify-content: center;
    font-family: "Archivo Black", "Arial Black", sans-serif; font-size: 20px; letter-spacing: 3px;
  }
  .services {
    position: absolute; left: 0; top: 152px; width: 100%; height: 116px;
    display: flex; gap: 20px; padding: 10px 26px 0;
    color: var(--white); font-size: 14px; line-height: 1.28;
  }
  .services ul { list-style: none; flex: 1; }
  .services li { position: relative; padding-left: 14px; }
  .services li::before { content: ""; position: absolute; left: 0; top: 6px; width: 6px; height: 6px; border-radius: 50%; background: var(--white); }
  .back .cta-band {
    position: absolute; left: 0; top: 268px; width: 100%; height: 52px;
    display: flex; flex-direction: column; align-items: center; justify-content: center;
  }
  .cta-note { font-style: italic; font-size: 12px; color: var(--graphite); }
  .cta-main { font-weight: 700; font-size: 17px; }
</style>
</head>
<body>

<section class="card front" aria-label="Business card front">
  <div class="texture" role="img" aria-label="Dark honeycomb metal texture"></div>
  <div class="truck-photo" role="img" aria-label="Black and white photo of a road train truck"></div>
  <div class="brand-name">Ridgeway<br>Haulage</div>

  <div class="identity-band silver">
    <div class="person">
      <div class="person-name">Daniel Harlow</div>
      <div class="person-role">Director</div>
    </div>
    <div class="divider"></div>
    <div class="links">
      <div>
        <svg viewBox="0 0 16 16"><rect x="1" y="3" width="14" height="10" fill="#111"/><path d="M1 3 L8 9 L15 3" stroke="#ddd" stroke-width="1.2" fill="none"/></svg>
        info@ridgewayhaul.com
      </div>
      <div>
        <svg viewBox="0 0 16 16"><circle cx="8" cy="8" r="7" fill="#111"/><g stroke="#ddd" stroke-width=".9" fill="none"><ellipse cx="8" cy="8" rx="3" ry="7"/><line x1="1" y1="8" x2="15" y2="8"/><line x1="2.5" y1="4.5" x2="13.5" y2="4.5"/><line x1="2.5" y1="11.5" x2="13.5" y2="11.5"/></g></svg>
        www.ridgewayhaul.com
      </div>
    </div>
  </div>

  <div class="phone-band">
    <div class="phone-icon">
      <svg viewBox="0 0 16 16"><path d="M4 1.5 L6.2 4.5 L5 6.3 C5.8 8 7.9 10.2 9.7 11 L11.5 9.8 L14.5 12 L13 14.5 C7.5 14 2 8.5 1.5 3 Z" fill="#fff"/></svg>
    </div>
    <div class="phone-number">044-555 018 274</div>
  </div>

  <div class="address-band silver">17, Quarry Road, Northfield, 45890</div>
</section>

<section class="card back" aria-label="Business card back">
  <div class="texture" role="img" aria-label="Dark honeycomb metal texture"></div>
  <div class="brand-name">Ridgeway Haulage</div>

  <div class="services-title-band silver">OUR SERVICES</div>

  <div class="services">
    <ul>
      <li>Over Size Loads / Hot Shot Loads</li>
      <li>Heavy Vehicle Recovery Services</li>
      <li>Potable Water Deliveries</li>
      <li>Road Building / Maintenance</li>
      <li>Earthworks</li>
      <li>Sand &amp; Metal Supply &amp; Cartage</li>
    </ul>
    <ul>
      <li>Road Train Tippers</li>
      <li>Road Train Tankers</li>
      <li>Road Train Flat Tops</li>
      <li>Drop Deck Trailers</li>
      <li>Mine Site accredited equipment &amp; Operators</li>
    </ul>
  </div>

  <div class="cta-band silver">
    <div class="cta-note">we offer a large range of services not listed so</div>
    <div class="cta-main">Call us today for a personalised quote to suit your needs.</div>
  </div>
</section>

</body>
</html>
```